Machining Business Order Thank You Insert

I am looking for a business style card to include with orders that I ship. The card needs to thank the recipient for their order, and encourage them to leave a review. The card should include my business name and contact information and have an area to hand write a message.

I mainly sale on Craftlane and my own website. We are a machining an manufacturing business that are in the sale of mostly metal machined and 3d printed plastic products.

The front of the card should include the following:
Logo: (attached)
Snapgram: https://www.snapgram.example/kelvomill/
Friendsbook: https://www.friendsbook.example/KelvoMill
Website: https://www.kelvomill.example/

The back of the card needs an area to write a message

Industry/Entity Type

3D Printing, Machining, Craftlane

Contact Information for Business Card

Black or white front, white back to write a personal message

Font styles to use
Sans Serif

Colors

Designer to choose colors to be used in the design.

Requirements
Must have
• Encourage a review, social media info

```html
<!DOCTYPE html>
<html lang="en">
<head>
<meta charset="UTF-8">
<title>KelvoMill – Order Thank You Card</title>
<link href="https://fonts.googleapis.com/css2?family=Exo+2:wght@400;600&family=Open+Sans:wght@400;600;700&display=swap" rel="stylesheet">
<style>
  :root {
    --stage: #d6d6d4;
    --card-black: #1f1f1f;
    --card-black-soft: #2c2b2a;
    --accent: #f05a28;
    --steel: #9a9a9a;
    --text-light: #e6e6e6;
    --paper: #f4f4f4;
    --ink-grey: #6b6b6b;
  }
  * { margin: 0; padding: 0; box-sizing: border-box; }
  html, body { width: 1200px; height: 675px; overflow: hidden; }
  body {
    background: var(--stage);
    font-family: "Open Sans", Arial, sans-serif;
    display: flex;
    align-items: center;
    justify-content: center;
    gap: 40px;
  }
  .card {
    position: relative;
    width: 540px;
    height: 310px;
    border-radius: 14px;
    overflow: hidden;
    box-shadow: 0 6px 18px rgba(0,0,0,0.18);
  }

  /* Brand lockup */
  .brand {
    position: absolute;
    left: 50%;
    transform: translateX(-50%);
    display: flex;
    align-items: center;
    gap: 12px;
    white-space: nowrap;
  }
  .brand-square {
    width: 34px;
    height: 34px;
    background: var(--accent);
  }
  .brand-name {
    font-family: "Exo 2", Arial, sans-serif;
    font-weight: 400;
    font-size: 26px;
    letter-spacing: 7px;
    color: var(--steel);
  }

  /* Back: message card */
  .card-back {
    background: linear-gradient(160deg, var(--card-black-soft), var(--card-black));
  }
  .card-back .brand { top: 36px; }
  .thanks {
    position: absolute;
    top: 96px;
    left: 0; right: 0;
    text-align: center;
    font-size: 15px;
    font-weight: 600;
    letter-spacing: 0.5px;
    color: var(--accent);
  }
  .message-band {
    position: absolute;
    left: 0; right: 0;
    top: 140px;
    height: 130px;
    background: var(--paper);
  }
  .message-label {
    position: absolute;
    top: 10px;
    left: 50%;
    transform: translateX(-50%);
    font-size: 13px;
    font-weight: 600;
    letter-spacing: 1px;
    color: var(--ink-grey);
  }
  .review-note {
    position: absolute;
    left: 0; right: 0;
    top: 270px;
    height: 40px;
    display: flex;
    align-items: center;
    justify-content: center;
    font-size: 12px;
    color: var(--text-light);
  }
  .review-note strong { color: var(--accent); font-weight: 600; margin: 0 4px; }

  /* Front: contact card */
  .card-front {
    background: linear-gradient(200deg, var(--card-black-soft), var(--card-black));
    color: var(--text-light);
  }
  .card-front .brand { top: 32px; }
  .social-list {
    position: absolute;
    top: 94px;
    left: 34px;
    list-style: none;
    display: flex;
    flex-direction: column;
    gap: 8px;
    font-size: 12px;
  }
  .social-list li, .contact-list li {
    display: flex;
    align-items: center;
    gap: 8px;
  }
  .network { color: var(--steel); width: 78px; }
  .icon {
    width: 16px;
    height: 16px;
    flex: none;
  }
  .divider {
    position: absolute;
    left: 24px;
    right: 24px;
    top: 190px;
    height: 2px;
    background: var(--accent);
  }
  .contact-list {
    position: absolute;
    top: 210px;
    left: 34px;
    list-style: none;
    display: flex;
    flex-direction: column;
    gap: 8px;
    font-size: 13px;
  }
  .person {
    position: absolute;
    right: 34px;
    top: 206px;
    text-align: right;
  }
  .person-name {
    font-size: 22px;
    font-weight: 700;
    letter-spacing: 1px;
    color: var(--accent);
  }
  .person-role {
    font-size: 12px;
    color: var(--text-light);
  }
</style>
</head>
<body>

  <section class="card card-back" aria-label="Card back with message area">
    <div class="brand">
      <span class="brand-square"></span>
      <span class="brand-name">KELVOMILL</span>
    </div>
    <p class="thanks">Thank you for your order!</p>
    <div class="message-band">
      <span class="message-label">MESSAGE</span>
    </div>
    <p class="review-note">Enjoying it? Please leave us a review on<strong>Craftlane</strong></p>
  </section>

  <section class="card card-front" aria-label="Card front with contact details">
    <div class="brand">
      <span class="brand-square"></span>
      <span class="brand-name">KELVOMILL</span>
    </div>

    <ul class="social-list">
      <li>
        <svg class="icon" viewBox="0 0 16 16" aria-hidden="true">
          <circle cx="8" cy="8" r="7" fill="var(--accent)"/>
        </svg>
        <span class="network">Friendsbook</span>
        friendsbook.example/KelvoMill
      </li>
      <li>
        <svg class="icon" viewBox="0 0 16 16" aria-hidden="true">
          <circle cx="8" cy="8" r="7" fill="var(--accent)"/>
        </svg>
        <span class="network">Snapgram</span>
        snapgram.example/kelvomill
      </li>
      <li>
        <svg class="icon" viewBox="0 0 16 16" aria-hidden="true">
          <rect width="16" height="16" rx="3" fill="var(--accent)"/>
          <circle cx="8" cy="8" r="4.5" fill="none" stroke="#1f1f1f" stroke-width="1.3"/>
          <line x1="3.5" y1="8" x2="12.5" y2="8" stroke="#1f1f1f" stroke-width="1.1"/>
          <ellipse cx="8" cy="8" rx="2" ry="4.5" fill="none" stroke="#1f1f1f" stroke-width="1.1"/>
        </svg>
        <span class="network">Website</span>
        www.kelvomill.example
      </li>
    </ul>

    <div class="divider"></div>

    <ul class="contact-list">
      <li>
        <svg class="icon" viewBox="0 0 16 16" aria-hidden="true">
          <rect width="16" height="16" rx="3" fill="var(--accent)"/>
          <path d="M8 3.2a3 3 0 0 0-3 3c0 2.3 3 6 3 6s3-3.7 3-6a3 3 0 0 0-3-3z" fill="#1f1f1f"/>
          <circle cx="8" cy="6.2" r="1.1" fill="var(--accent)"/>
        </svg>
        Harlow Springs, Indiana
      </li>
      <li>
        <svg class="icon" viewBox="0 0 16 16" aria-hidden="true">
          <rect width="16" height="16" rx="3" fill="var(--accent)"/>
          <rect x="5" y="3" width="6" height="10" rx="1.2" fill="none" stroke="#1f1f1f" stroke-width="1.3"/>
          <line x1="7" y1="11" x2="9" y2="11" stroke="#1f1f1f" stroke-width="1.1"/>
        </svg>
        xxx-xxx-xxxx
      </li>
    </ul>

    <div class="person">
      <div class="person-name">NAME</div>
      <div class="person-role">Designation</div>
    </div>
  </section>

</body>
</html>
```